Large online photo magazine needs redesign

We have previously digitised a historical photographic magazine of around 20,000 printed pages and made it available online. The magazine ran up to the early 1970s, and the content is largely black and white photographs of local events, accompanied by short captions.

Although the content is very rich, the design needs to be revisited so that:
* it is visually appealing
* it is responsive (i.e. works in browsers across all manner of devices)
* is faithful to the nature of the content

There are only a few core page types, and the central one is the article page, an example of which can be seen at:
http://snapgazette.example/gisborne/issue/KLR48_19600714/t1-body-d4.html

Any design submitted should be based on the treatment of an article page such as the above.

Given the large number of pages on our site, we need a design which can be templated to work for any content in the collection, i.e. we cannot hand-craft our templates to match a given page of content, rather a template must work acceptably well for all content.

The current site, although basic in design, has the advantage that it is quite efficient in the amount of data per page request (around 100k - 200k). While not adverse to web fonts, banner imagery etc, we will carefully consider the benefit gained from any such treatment against the amount of extra data that needs to be downloaded to the client's browser.

For the right design, we are able ourselves to adapt it to a CSS layout.

An example of each core page type is as follows (though for this project we only expect a design for a single page, as itemised above):

http://snapgazette.example/gisborne/index.html
http://snapgazette.example/gisborne/about.html
http://snapgazette.example/gisborne/help.html
http://snapgazette.example/gisborne/initial/index.html
http://snapgazette.example/gisborne/search/results?type=section&text=smith&cmdSubmit=Go
http://snapgazette.example/gisborne/advanced-search/index.html
http://snapgazette.example/gisborne/issue/KLR48_19600714/t1-front-d1.html
http://snapgazette.example/gisborne/issue/KLR48_19600714/index.html
http://snapgazette.example/gisborne/issue/KLR48_19600714/fig-KLR48_19600714_005a.html
http://snapgazette.example/gisborne/issue/KLR48_19600714/KLR48_19600714_012.html
http://snapgazette.example/gisborne/issue/KLR48_19600714/thumbnails.html

Target Market(s)

A general browsing audience of all ages, but skewed towards the older generations, and those interested in family / regional history.

The average user will not be particularly web-savy, and the treatment of the content should not detract / distract from the actual content itself.

Industry/Entity Type

Events

Requirements
Must have
• * it is visually appealing
The content should be visually appealing to the audience, which can be defined as a general browsing audience of all ages, but skewed towards the middle and older generations.

* it is responsive (the design can be adapted - by us - to work in browsers across all manner of devices)

The magazine covers (http://snapgazette.example/gisborne/issues/index.html) offer some possible inspiration for treatment of the material.

```html
<!DOCTYPE html>
<html lang="en">
<head>
<meta charset="utf-8">
<title>Flying Sisters from Gisborne – Snap Gazette</title>
<link href="https://fonts.googleapis.com/css2?family=Roboto:wght@300;400;700&display=swap" rel="stylesheet">
<style>
  :root {
    --brand-red: #c93a4d;
    --brand-red-dark: #3a1518;
    --nav-active: #2a0e10;
    --stage-black: #000;
    --page-grey: #e4e4e4;
    --footer-grey: #d2d2d2;
    --button-grey: #7d7d7d;
    --text-grey: #666;
    --footer-text: #777;
    --white: #fff;
    --sepia-light: #d9d4c4;
    --sepia-dark: #4a463e;
  }
  * { box-sizing: border-box; margin: 0; padding: 0; }
  html, body { width: 768px; height: 1200px; overflow: hidden; }
  body { position: relative; background: var(--page-grey); font-family: 'Roboto', Arial, sans-serif; color: var(--text-grey); }
  a { color: inherit; text-decoration: none; }

  .site-header { position: absolute; top: 0; left: 0; width: 768px; height: 75px; background: var(--brand-red); }
  .brand { position: absolute; left: 60px; top: 24px; color: var(--white); font-weight: 700; font-size: 28px; letter-spacing: 1px; }
  .utility-links { position: absolute; right: 58px; top: 13px; font-size: 9px; color: #f4d3d7; display: flex; gap: 12px; }

  .main-nav { position: absolute; top: 75px; left: 0; width: 768px; height: 32px; background: var(--brand-red-dark); }
  .main-nav ul { list-style: none; display: flex; position: absolute; left: 62px; top: 0; height: 32px; }
  .main-nav li { font-size: 10px; color: var(--white); padding: 0 10px; line-height: 32px; }
  .main-nav li.active { background: var(--nav-active); color: #ef5a6c; }
  .search-box { position: absolute; left: 541px; top: 7px; width: 170px; height: 19px; background: var(--white); }
  .search-box span { position: absolute; left: 8px; top: 4px; font-size: 9px; color: #c8c8c8; }
  .search-box svg { position: absolute; right: 2px; top: 2px; }

  .page-stage { position: absolute; top: 107px; left: 0; width: 768px; height: 338px; background: var(--stage-black); overflow: hidden; }
  .issue-title { position: absolute; top: 24px; width: 100%; text-align: center; color: var(--white); font-weight: 300; font-size: 17px; }
  .page-side { position: absolute; top: 60px; height: 254px; background: linear-gradient(90deg, #2b2a27, #3d3a34, #2a2926); opacity: .8; }
  .page-side.left { left: 0; width: 162px; }
  .page-side.right { left: 582px; width: 186px; }
  .spread { position: absolute; left: 173px; top: 56px; width: 400px; height: 259px; display: flex; }
  .spread-left { width: 200px; height: 100%; background: linear-gradient(160deg, var(--sepia-light), #9d998d 60%, var(--sepia-light)); }
  .spread-right { width: 200px; height: 100%; background: linear-gradient(170deg, #e89a9b, #c77a7a 55%, #e8a4a2); }
  .stage-btn { position: absolute; top: 152px; width: 100px; height: 36px; background: var(--brand-red); color: var(--white); font-size: 9px; display: flex; align-items: center; gap: 8px; justify-content: center; }
  .stage-btn.prev { left: 29px; }
  .stage-btn.next { left: 626px; }

  .article-tools { position: absolute; left: 0; width: 768px; height: 25px; }
  .article-tools.top { top: 492px; }
  .article-tools.bottom { top: 1047px; }
  .tool-btn { position: absolute; top: 0; height: 25px; background: var(--button-grey); color: var(--white); font-size: 10px; display: flex; align-items: center; justify-content: center; gap: 5px; }
  .tool-btn.current { background: var(--brand-red); }
  .tool-prev { left: 312px; width: 93px; }
  .tool-next { left: 422px; width: 72px; }
  .tool-contents { left: 513px; width: 76px; }
  .tool-print { left: 607px; width: 102px; }

  .article { position: absolute; left: 58px; top: 526px; width: 652px; height: 506px; background: var(--white); }
  .article-title { position: absolute; top: 16px; width: 100%; text-align: center; color: var(--brand-red); font-weight: 300; font-size: 26px; }
  .article p { position: absolute; font-size: 11.2px; font-weight: 300; line-height: 16.2px; color: var(--text-grey); }
  .photo { position: absolute; }
  .photo.hostesses { left: 43px; top: 73px; width: 139px; height: 110px; background: linear-gradient(135deg, #d8d6d0, #5a5852 55%, #2b2a28); }
  .photo.hostess { left: 456px; top: 194px; width: 149px; height: 147px; background: linear-gradient(150deg, #cfcbbf, #4e4b44 60%, #77736a); }
  .photo.bridge { left: 50px; top: 377px; width: 169px; height: 95px; background: linear-gradient(180deg, #e2e0d6, #8b887c 55%, #3f3d36); border: 1px solid #b9b6aa; }
  .text-one { left: 201px; top: 94px; width: 420px; }
  .text-two { left: 49px; top: 224px; width: 394px; }
  .text-three { left: 233px; top: 391px; width: 395px; }

  .site-footer { position: absolute; top: 1094px; left: 0; width: 768px; height: 106px; background: var(--footer-grey); }
  .footer-links { position: absolute; left: 64px; top: 18px; display: flex; gap: 19px; font-size: 10px; color: var(--footer-text); }
  .social { position: absolute; left: 62px; top: 47px; display: flex; gap: 5px; }
  .social span { width: 27px; height: 27px; border-radius: 50%; background: #6f6f6f; border: 2px solid #8f8f8f; }
  .licence-badge { position: absolute; left: 647px; top: 19px; width: 60px; height: 20px; background: #1c1c1c; border: 1px solid #999; }
  .copyright { position: absolute; right: 61px; top: 50px; font-size: 10px; color: var(--footer-text); }
</style>
</head>
<body>
  <header class="site-header">
    <a class="brand" href="http://snapgazette.example/gisborne/index.html">Snap Gazette</a>
    <nav class="utility-links">
      <a href="http://snapgazette.example/gisborne/advanced-search/index.html">Advanced search</a>
      <a href="http://snapgazette.example/gisborne/help.html">Help</a>
      <a href="#">Report an Error</a>
    </nav>
  </header>

  <nav class="main-nav">
    <ul>
      <li class="active">HOME</li>
      <li>ABOUT</li>
      <li>BROWSE</li>
      <li>SNAP GAZETTE</li>
      <li>A-Z PEOPLE</li>
    </ul>
    <div class="search-box">
      <span>Search</span>
      <svg width="15" height="15" viewBox="0 0 15 15"><circle cx="6" cy="6" r="4.3" fill="none" stroke="#333" stroke-width="2"/><line x1="9.2" y1="9.2" x2="13.5" y2="13.5" stroke="#333" stroke-width="2.4"/></svg>
    </div>
  </nav>

  <section class="page-stage">
    <h1 class="issue-title">NO 73 JULY 14, 1960</h1>
    <div class="page-side left" role="img" aria-label="Previous magazine page, dimmed"></div>
    <div class="page-side right" role="img" aria-label="Next magazine page, dimmed"></div>
    <div class="spread">
      <div class="spread-left" role="img" aria-label="Magazine page of engagement portraits with captions"></div>
      <div class="spread-right" role="img" aria-label="Highlighted magazine page with air hostess photos and a river bridge"></div>
    </div>
    <a class="stage-btn prev" href="#"><svg width="16" height="12" viewBox="0 0 16 12"><path d="M15 6H2M7 1L2 6l5 5" fill="none" stroke="#fff" stroke-width="2"/></svg>PREVIOUS PAGE</a>
    <a class="stage-btn next" href="#">NEXT PAGE<svg width="16" height="12" viewBox="0 0 16 12"><path d="M1 6h13M9 1l5 5-5 5" fill="none" stroke="#fff" stroke-width="2"/></svg></a>
  </section>

  <div class="article-tools top">
    <a class="tool-btn tool-prev" href="#">❮ Previous Article</a>
    <a class="tool-btn tool-next current" href="#">Next Article ❯</a>
    <a class="tool-btn tool-contents" href="http://snapgazette.example/gisborne/issue/KLR48_19600714/index.html">Issue Contents</a>
    <a class="tool-btn tool-print" href="#"><svg width="14" height="12" viewBox="0 0 14 12"><rect x="3" y="0" width="8" height="3" fill="#fff"/><rect x="0" y="3.5" width="14" height="5.5" rx="1" fill="#fff"/><rect x="3" y="7" width="8" height="5" fill="#fff" stroke="#7d7d7d"/></svg>Print This Article</a>
  </div>

  <article class="article">
    <h2 class="article-title">Flying Sisters from Gisborne</h2>
    <div class="photo hostesses" role="img" aria-label="Photograph of three sisters in air hostess uniforms"></div>
    <p class="text-one">This is probably something of a record--three sisters who are all air hostesses. They are the Harlow sisters.....Corinne, Ida, and Lorna, daughters of Mr and Mrs W. G. Harlow, Kowhai Road, Gisborne.</p>
    <p class="text-two">And this young lady, Mavis Thorne, of Auckland, has made history in another way. She was the first air hostess to make a scheduled flight to Gisborne, on Sunday of last week. Hostess service has been extended by C.A.S. to include Gisborne flights, beginning with the Sunday Services.</p>
    <div class="photo hostess" role="img" aria-label="Photograph of an air hostess at an aircraft doorway"></div>
    <div class="photo bridge" role="img" aria-label="Photograph of the old highway bridge across the river"></div>
    <p class="text-three">The old highway bridge across the Waiapu River near Ruatoria probably has more Bailey "splints" than any other bridge in the country. It is to be replaced soon by a modern structure two miles downstream, after which all main-route traffic will pass through Ruatoria township. (Picture, Eastland).</p>
  </article>

  <div class="article-tools bottom">
    <a class="tool-btn tool-prev" href="#">❮ Previous Article</a>
    <a class="tool-btn tool-next" href="#">Next Article ❯</a>
    <a class="tool-btn tool-contents" href="http://snapgazette.example/gisborne/issue/KLR48_19600714/index.html">Issue Contents</a>
    <a class="tool-btn tool-print" href="#"><svg width="14" height="12" viewBox="0 0 14 12"><rect x="3" y="0" width="8" height="3" fill="#fff"/><rect x="0" y="3.5" width="14" height="5.5" rx="1" fill="#fff"/><rect x="3" y="7" width="8" height="5" fill="#fff" stroke="#7d7d7d"/></svg>Print This Article</a>
  </div>

  <footer class="site-footer">
    <nav class="footer-links">
      <a href="http://snapgazette.example/gisborne/index.html">Home</a>
      <a href="http://snapgazette.example/gisborne/about.html">About</a>
      <a href="http://snapgazette.example/gisborne/issues/index.html">Browse</a>
      <a href="#">Snap Gazette</a>
      <a href="http://snapgazette.example/gisborne/initial/index.html">A-Z people</a>
    </nav>
    <div class="social"><span></span><span></span><span></span><span></span></div>
    <div class="licence-badge"></div>
    <p class="copyright">© 2012 Harbourside Memorial Library</p>
  </footer>
</body>
</html>
```